Stationery Design Project for Marketing Consultancy

I have started a new consultancy business and require the following elements to be designed using existing logo:
• Business card
• Letterhead
• Envelope (DL, C4, C5)
• Microsoft word template for report writing
• A4 Presentation Folder
• Powerpoint template
COPY FOR FRONT AND BACK OF BUSINESS CARD
logo
'Measurable Marketing. Epic Results' slogan (but no need to use existing lockup with logo)
name, B Bus. Mktg, Grad Dip Digital Mktg, CPM (post nominal abbreviations in smaller font)
mobile: 04XX-XXX-XXX (I will give details to the winner to add)
website: www.tolvarin.com.au
email: info@tolvarin.com.au
COPY FOR LETTERHEAD
Logo
Company Name
Please, submit your designs that include business card, letterhead and envelope. Once selected the winner will be asked to complete the project by creating the rest of the artwork.
FINAL FILES
Print ready files to be supplied as well as Indesign files so that minor amends can be made if necessary in future.
• Layered vectors in EPS & PDF
• Screen quality JPEG & PNGs
ABOUT THE BUSINESS: TOLVARIN
I work with clients to understand their business challenges, developing and executing measurable marketing strategies tied to key business metrics. Services include:
Services include:
• Business planning and business development
• Marketing and brand strategy
• Insight-driven integrated campaigns
• Loyalty programs and retention marketing
• Marketing automation
• Direct marketing (traditional and digital)
• Content strategy and development
Hi everyone,
Target Market(s)
Corporate decision makers (heads of marketing, general managers etc) and small to medium sized business owners. Predominately male aged 35+
Industry/Entity Type
Marketing
Requirements
Must have
- BRAND PERSONALITY
The successful design will communicate brand personality. I am a professional, results-driven entrepreneur, but want to show off my creative flair.
MEMORABILITY
Looking for a unique and eye-catching design. Am considering special printing effects (die cuts, letterpress, interactive elements, embossing, foiling etc) or a striking minimalist approach.
Nice to have
- I have a mission that could be incorporated on reverse if room -
Turning insights into actions & passion into profit.
Should not have
- Use of pink or green.

```html
<!DOCTYPE html>
<html lang="en">
<head>
<meta charset="utf-8">
<title>Tolvarin Business Card</title>
<link rel="stylesheet" href="https://fonts.googleapis.com/css2?family=Montserrat:wght@600;700&family=Questrial&display=swap">
<style>
  :root {
    --backdrop: #1c1c1d;
    --card: #fbfbfa;
    --ink: #3b3b3c;
    --ink-soft: #555557;
    --mark: #3b3b3c;
  }
  * { margin: 0; padding: 0; box-sizing: border-box; }
  html, body {
    width: 1200px;
    height: 800px;
    overflow: hidden;
    background: var(--backdrop);
  }
  .canvas {
    position: relative;
    width: 1200px;
    height: 800px;
    display: flex;
    align-items: center;
    justify-content: center;
  }
  .business-card {
    position: relative;
    width: 960px;
    height: 548px;
    background: var(--card);
    color: var(--ink);
  }
  .brand {
    position: absolute;
    left: 118px;
    top: 250px;
    display: flex;
    flex-direction: column;
    align-items: flex-start;
  }
  .brand-lockup {
    display: flex;
    align-items: center;
    gap: 16px;
  }
  .brand-dot {
    width: 44px;
    height: 44px;
    border-radius: 50%;
    background: var(--mark);
  }
  .brand-name {
    font-family: "Montserrat", sans-serif;
    font-weight: 700;
    font-size: 50px;
    letter-spacing: 1px;
    line-height: 1;
    color: var(--mark);
  }
  .brand-slogan {
    margin-top: 10px;
    font-family: "Montserrat", sans-serif;
    font-weight: 700;
    font-size: 15px;
    letter-spacing: 0.3px;
    color: var(--mark);
  }
  .contact-block {
    position: absolute;
    left: 548px;
    top: 176px;
  }
  .person-name {
    font-family: "Montserrat", sans-serif;
    font-weight: 700;
    font-size: 22px;
    letter-spacing: 0.5px;
    color: var(--ink);
  }
  .person-title {
    margin-top: 4px;
    font-family: "Questrial", sans-serif;
    font-size: 18px;
    color: var(--ink-soft);
  }
  .contact-list {
    list-style: none;
    margin-top: 40px;
    margin-left: 28px;
  }
  .contact-item {
    display: flex;
    align-items: center;
    gap: 14px;
    height: 32px;
    font-family: "Questrial", sans-serif;
    font-size: 19px;
    color: var(--ink-soft);
  }
  .contact-icon {
    width: 22px;
    height: 22px;
    flex: none;
  }
</style>
</head>
<body>
<main class="canvas">
  <section class="business-card" aria-label="Tolvarin business card">
    <div class="brand">
      <div class="brand-lockup">
        <span class="brand-dot"></span>
        <span class="brand-name">TOLVARIN</span>
      </div>
      <p class="brand-slogan">CLEAR STRATEGY. PROVEN GROWTH NOW.</p>
    </div>

    <div class="contact-block">
      <h1 class="person-name">DANIEL HARLOW</h1>
      <p class="person-title">Manging Director</p>
      <ul class="contact-list">
        <li class="contact-item">
          <svg class="contact-icon" viewBox="0 0 22 22" aria-hidden="true">
            <circle cx="11" cy="11" r="10" fill="none" stroke="#555557" stroke-width="1.3"/>
            <rect x="8" y="5.5" width="6" height="11" rx="1" fill="none" stroke="#555557" stroke-width="1.2"/>
            <line x1="10" y1="14.5" x2="12" y2="14.5" stroke="#555557" stroke-width="1"/>
          </svg>
          <span>+0400-555-019</span>
        </li>
        <li class="contact-item">
          <svg class="contact-icon" viewBox="0 0 22 22" aria-hidden="true">
            <circle cx="11" cy="11" r="10" fill="#555557"/>
            <rect x="6" y="7.5" width="10" height="7" fill="none" stroke="#fbfbfa" stroke-width="1.2"/>
            <polyline points="6,7.5 11,11.5 16,7.5" fill="none" stroke="#fbfbfa" stroke-width="1.2"/>
          </svg>
          <span>info@tolvarin.com.au</span>
        </li>
        <li class="contact-item">
          <svg class="contact-icon" viewBox="0 0 22 22" aria-hidden="true">
            <circle cx="11" cy="11" r="9.5" fill="none" stroke="#555557" stroke-width="1.3"/>
            <ellipse cx="11" cy="11" rx="4" ry="9.5" fill="none" stroke="#555557" stroke-width="1.1"/>
            <line x1="1.5" y1="11" x2="20.5" y2="11" stroke="#555557" stroke-width="1.1"/>
            <line x1="3" y1="6.5" x2="19" y2="6.5" stroke="#555557" stroke-width="1"/>
            <line x1="3" y1="15.5" x2="19" y2="15.5" stroke="#555557" stroke-width="1"/>
          </svg>
          <span>www.tolvarin.com.au</span>
        </li>
      </ul>
    </div>
  </section>
</main>
</body>
</html>
```